Venture 482 - Lumora Book Cover

I am looking for a Lumora book cover for my book about "Venture 482".
The Book is Titled:
Venture 482 Ascended
Shaping Outcomes: Paths To Unlocking Cosmic Truths
Author is Dorian Pell
Here is a book description that may help you understand more about it:
Inspired by the genius of Edwin Marlowe, this comprehensive guide delves into the ancient wisdom and cutting-edge science behind the 482 method, a powerful tool for manifesting your desires. Whether you're seeking personal growth, financial success, or spiritual enlightenment, this book provides advanced techniques and methods to transform your dreams into reality.
Any questions please ask.
Thanks
Owen

```html
<!DOCTYPE html>
<html lang="en">
<head>
<meta charset="UTF-8">
<title>Venture 482 Ascended — Book Cover</title>
<link rel="stylesheet" href="https://fonts.googleapis.com/css2?family=Cormorant+Garamond:ital,wght@0,500;0,600;1,500&display=swap">
<style>
  :root {
    --backdrop: #ebebeb;
    --space-deep: #120a33;
    --space-mid: #2a1a6e;
    --nebula: #7a5cc8;
    --nebula-glow: #a68ee6;
    --title-edge: #8c82da;
    --title-core: #eeeaff;
    --ink-light: #f4f2ff;
  }
  html, body {
    margin: 0;
    width: 1200px;
    height: 1200px;
    overflow: hidden;
    background: var(--backdrop);
  }
  .canvas {
    position: relative;
    width: 1200px;
    height: 1200px;
  }
  .cover {
    position: absolute;
    left: 219px;
    top: 29px;
    width: 761px;
    height: 1142px;
    overflow: hidden;
    font-family: "Cormorant Garamond", "Times New Roman", serif;
    color: var(--ink-light);
  }
  .cover-art {
    position: absolute;
    inset: 0;
    background:
      radial-gradient(ellipse 42% 36% at 50% 40%, rgba(166,142,230,0.45), rgba(166,142,230,0) 70%),
      linear-gradient(100deg, rgba(0,0,0,0) 38%, rgba(150,120,220,0.35) 50%, rgba(0,0,0,0) 62%),
      radial-gradient(ellipse 90% 70% at 50% 35%, var(--space-mid), var(--space-deep) 85%);
  }
  .series-line {
    position: absolute;
    top: 255px;
    left: 0;
    right: 0;
    text-align: center;
    font-size: 28px;
    font-weight: 500;
    letter-spacing: 0.1em;
    line-height: 1;
  }
  .series-line .series-number {
    font-style: italic;
  }
  .title {
    position: absolute;
    left: 0;
    right: 0;
    margin: 0;
    text-align: center;
    font-weight: 500;
    font-size: 150px;
    line-height: 1;
    background: linear-gradient(90deg, var(--title-edge) 10%, var(--title-core) 50%, var(--title-edge) 90%);
    -webkit-background-clip: text;
    background-clip: text;
    color: transparent;
  }
  .title-first { top: 318px; }
  .title-second { top: 452px; }
  .subtitle {
    position: absolute;
    top: 905px;
    left: 0;
    right: 0;
    text-align: center;
    font-size: 35px;
    font-weight: 500;
    letter-spacing: 0.04em;
    line-height: 1;
  }
  .author {
    position: absolute;
    top: 1040px;
    left: 0;
    right: 0;
    text-align: center;
    font-size: 38px;
    font-weight: 500;
    letter-spacing: 0.08em;
    line-height: 1;
  }
</style>
</head>
<body>
  <div class="canvas">
    <div class="cover">
      <div class="cover-art" role="img" aria-label="Purple starry night sky with a glowing nebula band and faint sacred geometry linework"></div>
      <div class="series-line">VENTURE <span class="series-number">482</span> ASCENDED</div>
      <h1 class="title title-first">Shaping</h1>
      <div class="title title-second">Outcomes</div>
      <div class="subtitle">Paths To Unlocking Cosmic Truths</div>
      <div class="author">DORIAN PELL</div>
    </div>
  </div>
</body>
</html>
```